Oriel Photography Business Card

I need a business card designed for a photography business based in Perth, Western Australia called Oriel Photography.

We specialise in wedding, event photography and portrait photography.

The business card must borrow the style of the attached logo.

The hex codes for the colours in the logo are:
#ED1D85 - Pink
#89C23E - Green
#37282F - Black

The name on the card will be:
Name: Tobrian
Phone: 0417395268
Website: www.orielphotography.example.com.au
Facebook: orielphotography

I am open and happy to accept creative concepts.

I’d like some space at the back for writing notes and appointment details.

```html
<!DOCTYPE html>
<html lang="en">
<head>
<meta charset="utf-8">
<title>Oriel Photography – Business Card</title>
<link href="https://fonts.googleapis.com/css2?family=Arimo:wght@400;700&display=swap" rel="stylesheet">
<style>
  :root {
    --page: #ffffff;
    --card-pink: #d95f87;
    --band-dark: #3a2e33;
    --brand-pink: #ed1d85;
    --brand-green: #89c23e;
    --brand-black: #37282f;
    --text-light: #ffffff;
    --contact-pink: #e8709b;
    --edge: #8a6b77;
  }
  * { margin: 0; padding: 0; box-sizing: border-box; }
  html, body {
    width: 1200px; height: 338px; overflow: hidden;
    background: var(--page);
    font-family: "Arimo", Arial, sans-serif;
  }
  .canvas { position: relative; width: 1200px; height: 338px; }

  .card {
    position: absolute; top: 0; height: 338px;
    background: var(--card-pink);
    overflow: hidden;
  }
  .card--front { left: 0; width: 576px; border: 1px solid var(--edge); }
  .card--back { left: 625px; width: 575px; }

  .holder-name {
    position: absolute; left: 32px; top: 64px;
    color: var(--text-light); font-weight: 700; font-size: 32px;
  }

  .brand-dot {
    position: absolute; border-radius: 50%;
    background: var(--brand-pink);
  }
  .brand-dot--front { left: 362px; top: 28px; width: 62px; height: 62px; }
  .brand-dot--faint { left: 31px; top: 142px; width: 96px; height: 96px; opacity: 0.22; }
  .brand-dot--back { left: 224px; top: 18px; width: 116px; height: 116px; }

  .brand-name {
    position: absolute; text-transform: uppercase;
    color: var(--brand-black); font-weight: 400; white-space: nowrap;
  }
  .brand-name--front { left: 262px; top: 107px; font-size: 10.5px; letter-spacing: 5.2px; }
  .brand-name--back { left: 0; width: 575px; text-align: center; top: 174px; font-size: 15px; letter-spacing: 12px; }

  .contact-band {
    position: absolute; left: 0; right: 0; bottom: 0; height: 83px;
    background: var(--band-dark);
  }
  .contact-line {
    position: absolute; left: 0; right: 0;
    display: flex; justify-content: center; align-items: center; gap: 10px;
    font-weight: 700; font-size: 15.5px; white-space: nowrap;
  }
  .contact-line--phone { top: 6px; color: var(--contact-pink); }
  .contact-line--web { top: 30px; color: var(--brand-green); }
  .contact-line--social { top: 54px; color: var(--contact-pink); }
  .contact-icon { width: 18px; height: 18px; flex: none; }
  .social-square { width: 15px; height: 15px; background: #4a6db0; border-radius: 2px; flex: none; }

  .write-field {
    position: absolute; left: 52px;
    color: var(--text-light); font-weight: 700; font-size: 16.5px;
  }
  .write-field--notes { top: 263px; }
  .write-field--appointment { top: 303px; }
</style>
</head>
<body>
<div class="canvas">

  <section class="card card--front" aria-label="Card front">
    <div class="holder-name">Tobrian</div>
    <div class="brand-dot brand-dot--front"></div>
    <div class="brand-name brand-name--front">Oriel Photography</div>
    <div class="brand-dot brand-dot--faint"></div>

    <div class="contact-band">
      <div class="contact-line contact-line--phone">
        <svg class="contact-icon" viewBox="0 0 18 18" aria-hidden="true">
          <rect x="0" y="0" width="18" height="18" rx="3" fill="#5b8fd6"/>
          <path d="M3 7c0-2 2-3 6-3s6 1 6 3l-2 1-1-2H6L5 8z" fill="#fff"/>
          <rect x="5" y="9" width="8" height="6" rx="1" fill="#fff"/>
        </svg>
        <span>0417395268</span>
      </div>
      <div class="contact-line contact-line--web">
        <svg class="contact-icon" viewBox="0 0 18 18" aria-hidden="true">
          <circle cx="9" cy="9" r="8" fill="#7fb0e0"/>
          <ellipse cx="9" cy="9" rx="3.5" ry="8" fill="none" stroke="#fff" stroke-width="1.2"/>
          <line x1="1" y1="9" x2="17" y2="9" stroke="#fff" stroke-width="1.2"/>
        </svg>
        <span>www.orielphotography.example.com.au</span>
      </div>
      <div class="contact-line contact-line--social">
        <span class="social-square"></span>
        <span>orielphotography</span>
      </div>
    </div>
  </section>

  <section class="card card--back" aria-label="Card back">
    <div class="brand-dot brand-dot--back"></div>
    <div class="brand-name brand-name--back">Oriel Photography</div>
    <div class="write-field write-field--notes">Notes :</div>
    <div class="write-field write-field--appointment">Appointment :</div>
  </section>

</div>
</body>
</html>
```